BildeVOLD buisnesscard

Hey :) I need a modern buisnesscard for my company BildeVOLD
It most have:
Dagligleder og Fotograf: Henrik Audun Strandvik

Mob: +4791264085
Epost: post@bildevold.example
Adresse: Kvernbakken9, 6040 Vikholmen

Facbook and instagram logo with text BildeVOLD

BildeVOLD logo

It Company

```html
<!DOCTYPE html>
<html lang="no">
<head>
<meta charset="utf-8">
<title>BildeVOLD – visittkort</title>
<link href="https://fonts.googleapis.com/css2?family=Inter:wght@400;500;700&display=swap" rel="stylesheet">
<style>
  :root {
    --page-bg: #ffffff;
    --page-border: #5a5a5a;
    --card-base: #4a0053;
    --card-band: #58046a;
    --card-shade: #430049;
    --text-main: #f0eaf2;
    --text-soft: #ded2e2;
    --text-contact: #c8b9cd;
  }
  * { box-sizing: border-box; margin: 0; padding: 0; }
  html, body { width: 1200px; height: 850px; overflow: hidden; }
  body {
    background: var(--page-bg);
    border: 1px solid var(--page-border);
    font-family: "Inter", Arial, sans-serif;
    position: relative;
  }
  .business-card {
    position: absolute;
    left: 325px;
    top: 267px;
    width: 550px;
    height: 315px;
    background: var(--card-base);
    overflow: hidden;
    text-align: center;
  }
  .card-backdrop { position: absolute; inset: 0; }
  .brand {
    position: absolute;
    left: 0; right: 0;
    top: 45px;
    display: flex;
    flex-direction: column;
    align-items: center;
    gap: 8px;
  }
  .brand-mark {
    width: 46px; height: 44px;
    background: var(--text-main);
  }
  .brand-name {
    color: var(--text-main);
    font-weight: 700;
    font-size: 19px;
    letter-spacing: 0.5px;
    line-height: 1;
  }
  .person-name {
    position: absolute;
    left: 0; right: 0; top: 145px;
    color: var(--text-main);
    font-size: 27px;
    font-weight: 500;
    line-height: 1.2;
  }
  .person-role {
    position: absolute;
    left: 0; right: 0; top: 182px;
    color: var(--text-soft);
    font-size: 18.5px;
    font-weight: 400;
  }
  .contact-list {
    position: absolute;
    left: 0; right: 0; top: 268px;
    display: flex;
    justify-content: center;
    gap: 15px;
    list-style: none;
    color: var(--text-contact);
    font-size: 13px;
  }
  .contact-item { display: flex; align-items: center; gap: 5px; white-space: nowrap; }
  .contact-icon { width: 10px; height: 10px; fill: var(--text-contact); }
  .contact-icon--mail { width: 12px; }
</style>
</head>
<body>
  <section class="business-card">
    <svg class="card-backdrop" viewBox="0 0 550 315" width="550" height="315" aria-hidden="true">
      <polygon points="0,0 4,0 290,315 0,315" fill="var(--card-band)"/>
      <polygon points="0,82 0,98 202,315 218,315" fill="var(--card-shade)"/>
      <polygon points="54,237 54,315 130,315" fill="var(--card-shade)"/>
    </svg>

    <div class="brand">
      <span class="brand-mark"></span>
      <span class="brand-name">BildeVOLD</span>
    </div>

    <h1 class="person-name">Henrik Audun Strandvik</h1>
    <p class="person-role">Dagligleder og Fotograf</p>

    <ul class="contact-list">
      <li class="contact-item">
        <svg class="contact-icon" viewBox="0 0 24 24"><path d="M6.6 10.8a15.1 15.1 0 0 0 6.6 6.6l2.2-2.2a1 1 0 0 1 1-.25 11.4 11.4 0 0 0 3.6.57 1 1 0 0 1 1 1V20a1 1 0 0 1-1 1A17 17 0 0 1 3 4a1 1 0 0 1 1-1h3.5a1 1 0 0 1 1 1c0 1.25.2 2.45.57 3.57a1 1 0 0 1-.25 1z"/></svg>
        +4791264085
      </li>
      <li class="contact-item">
        <svg class="contact-icon contact-icon--mail" viewBox="0 0 24 18"><path d="M0 0h24v2L12 10 0 2z M0 4l12 8 12-8v14H0z"/></svg>
        post@bildevold.example
      </li>
      <li class="contact-item">
        <svg class="contact-icon" viewBox="0 0 24 24"><path d="M23 1 1 11l10 2 2 10z"/></svg>
        Kvernbakken9, 6040 Vikholmen
      </li>
    </ul>
  </section>
</body>
</html>
```